General contractor/GM consaltant business card

I need a card for my contracting company in North Dakota, we build industrial buildings for the oil feild and oil feild related companies offices, shops, airplain hangars, airports ext. We have a familly atmosphere on the job and are very relational and personal.
Industry/Entity Type
Industrial
Contact Information for Business Card
Ridgepost Contractors LLC.
Derek T.Holloway
4837 Tamarind dr. Colorado Springs, CO. 80917
Cell# 406-555-0148
derek@ridgepostcontractors.com

```html
<!DOCTYPE html>
<html lang="en">
<head>
<meta charset="utf-8">
<title>Ridgepost Contractors LLC. – Business Card</title>
<link rel="stylesheet" href="https://fonts.googleapis.com/css2?family=Inter:wght@400;500&family=PT+Serif:wght@700&display=swap">
<style>
  :root {
    --page-bg: #e9e6e1;
    --card-bg: #ffffff;
    --brand-blue: #2255a4;
    --brand-red: #d8263a;
    --ink: #1c1c1c;
    --ink-soft: #333333;
  }
  html, body {
    margin: 0;
    padding: 0;
    width: 1200px;
    height: 858px;
    overflow: hidden;
    background: var(--page-bg);
  }
  .canvas {
    width: 1200px;
    height: 858px;
    display: flex;
    align-items: center;
    justify-content: center;
    gap: 50px;
  }
  .card {
    position: relative;
    width: 540px;
    height: 310px;
    background: linear-gradient(135deg, #ffffff 0%, #f3f3f3 100%);
    box-shadow: 0 10px 28px rgba(0,0,0,0.22);
    overflow: hidden;
    font-family: "Inter", Helvetica, Arial, sans-serif;
  }
  .card__band {
    position: absolute;
    left: 0; top: 0; bottom: 0;
    width: 22px;
    background: var(--brand-blue);
  }
  .card__rule {
    position: absolute;
    left: 27px; top: 0; bottom: 0;
    width: 3px;
    background: var(--brand-red);
  }
  .company-name {
    font-family: "PT Serif", Georgia, serif;
    font-weight: 700;
    margin: 0;
    position: absolute;
  }
  .front .company-name {
    left: 70px;
    top: 96px;
    font-size: 30px;
    color: var(--brand-red);
  }
  .front .holder-name {
    position: absolute;
    right: 34px;
    top: 26px;
    margin: 0;
    font-size: 22px;
    font-weight: 400;
    color: var(--ink);
  }
  .contact-list {
    position: absolute;
    left: 150px;
    top: 190px;
    margin: 0;
    padding: 0;
    list-style: none;
    font-size: 14px;
    line-height: 20px;
    color: var(--ink-soft);
  }
  .contact-list li {
    display: flex;
    align-items: center;
    gap: 10px;
  }
  .contact-list .no-icon { padding-left: 22px; }
  .contact-icon { width: 12px; height: 12px; flex: none; }
  .back .company-name {
    left: 0; right: 0;
    top: 128px;
    text-align: center;
    font-size: 36px;
    color: var(--brand-blue);
    padding-left: 30px;
  }
</style>
</head>
<body>
<main class="canvas">
  <section class="card front" aria-label="Card front">
    <div class="card__band"></div>
    <div class="card__rule"></div>
    <h1 class="company-name">Ridgepost Contractors LLC.</h1>
    <p class="holder-name">Derek T.Holloway</p>
    <ul class="contact-list">
      <li>
        <svg class="contact-icon" viewBox="0 0 12 12" aria-hidden="true"><rect x="3" y="0.5" width="6" height="11" rx="1" fill="none" stroke="#333" stroke-width="1.2"/><rect x="4.5" y="9" width="3" height="1" fill="#333"/></svg>
        <span>406-555-0148</span>
      </li>
      <li>
        <svg class="contact-icon" viewBox="0 0 12 12" aria-hidden="true"><rect x="0.6" y="2.5" width="10.8" height="7.5" fill="none" stroke="#333" stroke-width="1.2"/><path d="M0.8 2.8 L6 7 L11.2 2.8" fill="none" stroke="#333" stroke-width="1.2"/></svg>
        <span>derek@ridgepostcontractors.com</span>
      </li>
      <li>
        <svg class="contact-icon" viewBox="0 0 12 12" aria-hidden="true"><path d="M6 11.5 C2.5 7.5 2 6 2 4.5 A4 4 0 0 1 10 4.5 C10 6 9.5 7.5 6 11.5Z" fill="#333"/><circle cx="6" cy="4.5" r="1.5" fill="#fff"/></svg>
        <span>4837 Tamarind dr.</span>
      </li>
      <li class="no-icon"><span>Colorado Springs, CO. 80917</span></li>
    </ul>
  </section>

  <section class="card back" aria-label="Card back">
    <div class="card__band"></div>
    <div class="card__rule"></div>
    <h2 class="company-name">Ridgepost Contractors LLC.</h2>
  </section>
</main>
</body>
</html>
```